Redesign business cards

We have a new logo and I am not that happy with the layout of our existing card and looking for a change. Font is a bit small and the green can be hard to read. Logo may need a tidy up as the copy I have is not that hi-res too so require you to produce a hi-res version of the logo for us too. There will be three individual business cards to produce with just the names and phone numbers being different. Address will change too, but use what you see on the card for now.

Industry/Entity Type

Business

Requirements
Nice to have
• You could consider a redesign to the new logo, just not too radical. We like the blue and green hexagons as we feel that they are representative of oil industry that we are in.

```html
<!DOCTYPE html>
<html lang="en">
<head>
<meta charset="utf-8">
<title>Verdane Fluid Services – Business Card</title>
<link rel="stylesheet" href="https://fonts.googleapis.com/css2?family=Open+Sans:wght@400;600;700&display=swap">
<style>
  :root {
    --backdrop: #d9d4cc;
    --card-white: #ffffff;
    --brand-blue: #0aa6e6;
    --accent-orange: #f08a1c;
    --text-grey: #6b6b6b;
    --text-dark: #4a4a4a;
  }
  * { box-sizing: border-box; margin: 0; padding: 0; }
  html, body {
    width: 1200px; height: 829px; overflow: hidden;
    background: var(--backdrop);
    font-family: "Open Sans", Arial, sans-serif;
  }
  .canvas {
    width: 1200px; height: 829px;
    display: flex; align-items: center; justify-content: center; gap: 40px;
  }
  .card {
    width: 540px; height: 309px;
    position: relative;
    box-shadow: 0 6px 18px rgba(0,0,0,0.18);
  }
  /* Front */
  .card-front { background: var(--card-white); }
  .brand {
    position: absolute; top: 34px; right: 36px;
    display: flex; align-items: center; gap: 10px;
    color: var(--brand-blue); font-weight: 700; font-size: 26px; letter-spacing: -0.3px;
  }
  .brand-mark { width: 14px; height: 14px; border-radius: 50%; background: var(--brand-blue); }
  .person {
    position: absolute; top: 88px; right: 36px; text-align: right;
  }
  .person-name { color: var(--accent-orange); font-weight: 700; font-size: 16px; }
  .person-role { color: var(--text-grey); font-size: 12px; margin-top: 2px; }
  .contacts {
    position: absolute; top: 140px; right: 36px;
    list-style: none; text-align: right;
  }
  .contacts li {
    display: flex; align-items: center; justify-content: flex-end; gap: 7px;
    color: var(--text-dark); font-size: 12.5px; line-height: 22px;
  }
  .contacts svg { width: 13px; height: 13px; order: -1; }
  .address {
    position: absolute; left: 36px; bottom: 30px;
    color: var(--text-dark); font-size: 12.5px; line-height: 20px;
  }
  /* Back */
  .card-back { background: var(--brand-blue); color: #fff; }
  .back-brand {
    position: absolute; top: 110px; left: 0; right: 0; text-align: center;
    font-weight: 700; font-size: 34px; letter-spacing: -0.3px;
  }
  .back-web {
    position: absolute; bottom: 34px; left: 0; right: 0; text-align: center;
    font-size: 14px; letter-spacing: 3px;
  }
</style>
</head>
<body>
<main class="canvas">
  <section class="card card-front" aria-label="Card front">
    <div class="brand"><span class="brand-mark"></span>Verdane Fluid Services</div>
    <div class="person">
      <p class="person-name">Daniel Harwood NZCE (Mech) P&amp;P</p>
      <p class="person-role">Director</p>
    </div>
    <ul class="contacts">
      <li>+61 400 555 018
        <svg viewBox="0 0 14 14" aria-hidden="true"><circle cx="7" cy="7" r="7" fill="var(--accent-orange)"/><path d="M4.6 3.6l1.3 1.4-.7 1c.5 1 1.3 1.8 2.3 2.3l1-.7 1.4 1.3-.8 1.1C6.5 10 4 7.5 3.5 4.4z" fill="#fff"/></svg>
      </li>
      <li>daniel@verdane.com.au
        <svg viewBox="0 0 14 14" aria-hidden="true"><circle cx="7" cy="7" r="7" fill="var(--accent-orange)"/><rect x="3.5" y="4.5" width="7" height="5" fill="#fff"/><path d="M3.5 4.5L7 7.3l3.5-2.8" stroke="var(--accent-orange)" stroke-width="0.8" fill="none"/></svg>
      </li>
      <li>www.verdane.com.au
        <svg viewBox="0 0 14 14" aria-hidden="true"><circle cx="7" cy="7" r="7" fill="var(--accent-orange)"/><circle cx="7" cy="7" r="3.6" fill="none" stroke="#fff" stroke-width="0.9"/><path d="M3.4 7h7.2M7 3.4c-1.6 2-1.6 5.2 0 7.2M7 3.4c1.6 2 1.6 5.2 0 7.2" stroke="#fff" stroke-width="0.8" fill="none"/></svg>
      </li>
    </ul>
    <address class="address" style="font-style:normal">
      Verdane Fluid Services 412 Harbour Road<br>
      PO Box 5140 | Riverside Queensland 4000
    </address>
  </section>

  <section class="card card-back" aria-label="Card back">
    <p class="back-brand">Verdane</p>
    <p class="back-web">www.verdane.com.au</p>
  </section>
</main>
</body>
</html>
```